A clean crisp business card for a Landscape Construction company. Designed to be easy to read contact/ info and also be appealing/interesting, unlike a traditional business card.

Industry/Entity Type

Landscape Construction

Contact Information for Business Card

Company name : Brambleford Landscape Construction, phone number: (877) 62Vista, website:Bramblefordyards.example, Email, sales@bramblefordyards.example

Requirements
Nice to have
• Luxurious finishes/ details…. Icons or emblems next to contact info
Should not have
• Clipart or general pictures

```html
<!DOCTYPE html>
<html lang="en">
<head>
<meta charset="utf-8">
<title>Brambleford Landscape Construction — Business Card</title>
<link rel="stylesheet" href="https://fonts.googleapis.com/css2?family=Cinzel:wght@400;500&family=Arimo:wght@400&display=swap">
<style>
  :root {
    --backdrop: #3b3431;
    --card-black: #1c1c1d;
    --card-black-soft: #262627;
    --card-white: #ffffff;
    --leaf-green: #8cc63f;
    --water-blue: #2f7ccf;
    --emboss-grey: #3a3a3c;
    --contact-white: #f4f4f4;
  }
  * { box-sizing: border-box; margin: 0; padding: 0; }
  html, body {
    width: 1200px; height: 716px; overflow: hidden;
    background: var(--backdrop);
  }
  .canvas {
    position: relative; width: 1200px; height: 716px;
    display: flex; align-items: center; justify-content: center; gap: 40px;
  }
  .card {
    position: relative; width: 540px; height: 309px; overflow: hidden;
    box-shadow: 0 14px 30px rgba(0,0,0,.45);
  }
  /* Front */
  .card-front {
    background: linear-gradient(135deg, var(--card-black-soft), var(--card-black));
    border-right: 3px solid var(--leaf-green);
    border-bottom: 3px solid var(--leaf-green);
    display: flex; align-items: center; justify-content: center;
  }
  .front-wordmark {
    font-family: "Cinzel", serif; font-weight: 500;
    color: var(--emboss-grey); text-align: center; line-height: 1.15;
  }
  .front-wordmark .name { display: block; font-size: 46px; letter-spacing: 1px; }
  .front-wordmark .line { display: block; font-size: 15px; letter-spacing: 4px; }
  /* Back */
  .card-back {
    background: var(--card-white);
    border-bottom: 3px solid var(--leaf-green);
  }
  .card-back svg.swoosh { position: absolute; inset: 0; }
  .back-wordmark {
    position: absolute; left: 128px; top: 40px;
    font-family: "Cinzel", serif; font-weight: 500;
    color: var(--water-blue); line-height: 1.1;
  }
  .back-wordmark .name { display: block; font-size: 30px; }
  .back-wordmark .line { display: block; font-size: 10.5px; letter-spacing: 2.6px; }
  .person { position: absolute; left: 34px; top: 198px; font-family: "Cinzel", serif; }
  .person-name { color: var(--water-blue); font-size: 21px; letter-spacing: 1px; }
  .person-role { color: var(--leaf-green); font-size: 14px; letter-spacing: 1px; }
  .person-marker {
    position: absolute; left: 0; top: 204px; width: 0; height: 0;
    border-top: 7px solid transparent; border-bottom: 7px solid transparent;
    border-left: 10px solid var(--leaf-green);
  }
  .contact-list {
    position: absolute; right: 124px; top: 238px; list-style: none;
    font-family: "Arimo", sans-serif; font-size: 13.5px; color: var(--contact-white);
    text-align: right; line-height: 21px;
  }
  .contact-list li { display: flex; align-items: center; justify-content: flex-end; gap: 7px; }
  .contact-list svg { width: 11px; height: 11px; flex: none; }
</style>
</head>
<body>
<main class="canvas">
  <section class="card card-front" aria-label="Card front">
    <p class="front-wordmark">
      <span class="name">Brambleford</span>
      <span class="line">Landscape Construction</span>
    </p>
  </section>

  <section class="card card-back" aria-label="Card back">
    <svg class="swoosh" viewBox="0 0 540 309" aria-hidden="true">
      <path d="M0,70 C15,150 70,178 200,182 C340,188 460,200 500,309 L0,309 Z" fill="var(--card-black)"/>
      <path d="M8,55 C25,140 85,165 210,170 C340,176 440,186 485,228" fill="none" stroke="var(--water-blue)" stroke-width="7"/>
      <path d="M22,38 C40,122 110,148 230,155 C380,163 480,190 525,295" fill="none" stroke="var(--leaf-green)" stroke-width="14" stroke-linecap="round"/>
    </svg>
    <p class="back-wordmark">
      <span class="name">Brambleford</span>
      <span class="line">Landscape Construction</span>
    </p>
    <span class="person-marker"></span>
    <div class="person">
      <p class="person-name">DANIEL HARTLEY</p>
      <p class="person-role">DIRECTOR</p>
    </div>
    <ul class="contact-list">
      <li>(877) 62Vista
        <svg viewBox="0 0 12 12"><path d="M2.5 1l2 2.3-1 1.3c.7 1.5 1.9 2.7 3.4 3.4l1.3-1 2.3 2-1.2 1.5C5 10.2 1.8 7 .9 2.2z" fill="var(--leaf-green)"/></svg>
      </li>
      <li>sales@bramblefordyards.example
        <svg viewBox="0 0 12 12"><rect x="1" y="2.5" width="10" height="7" fill="none" stroke="var(--leaf-green)" stroke-width="1.2"/><path d="M1 2.5l5 4 5-4" fill="none" stroke="var(--leaf-green)" stroke-width="1.2"/></svg>
      </li>
      <li>www.bramblefordyards.example
        <svg viewBox="0 0 12 12"><circle cx="6" cy="6" r="5" fill="none" stroke="var(--leaf-green)" stroke-width="1.2"/><path d="M1 6h10M6 1c-2.5 3-2.5 7 0 10M6 1c2.5 3 2.5 7 0 10" fill="none" stroke="var(--leaf-green)" stroke-width="1"/></svg>
      </li>
    </ul>
  </section>
</main>
</body>
</html>
```